The Vantor Codex Book Cover

"The Vantor Codex" is a book I wrote with the slogan "Unlock Performance, Spark Engagement: Master the Art of Building Winning Cultures in Today's Hybrid World". The book is designed around a methodology that's mine and that I attached. I would love to see the graphic of the methodology integrated in the design in a very subtle way. Use colors from the model but the book cover should be catchy, modern and engaging to the eye.
Overall the book is about three key elements towards success:
- (Self) Directions (purpose)
- Human experience (people and psychological safety)
- Maximize engagement
The methodology is a FLOW so flow is something that could be incorporated as well in the concept.
Low design quality
Managers and Teams

```html
<!DOCTYPE html>
<html lang="en">
<head>
<meta charset="utf-8">
<title>The Vantor Codex — Book Cover</title>
<link rel="stylesheet" href="https://fonts.googleapis.com/css2?family=Abril+Fatface&family=Oswald:wght@600&family=Montserrat:wght@400;500&display=swap">
<style>
  :root {
    --backdrop: #dfe6ec;
    --paper: #f4f4f4;
    --ink: #111111;
    --teal: #3f9a9f;
    --teal-deep: #2c7a80;
    --pink: #e77f95;
    --violet: #6a5aa6;
    --sky: #5fa6d6;
    --lime: #c7cf3d;
    --aqua: #38c6c2;
    --gold: #f0c24a;
  }
  * { margin: 0; padding: 0; box-sizing: border-box; }
  html, body {
    width: 1200px; height: 1182px; overflow: hidden;
    background: var(--backdrop);
  }
  .cover {
    position: absolute; left: 230px; top: 36px;
    width: 740px; height: 1110px;
    background: linear-gradient(135deg, #fafafa 0%, var(--paper) 60%, #ececec 100%);
    box-shadow: 0 10px 30px rgba(0,0,0,.12);
    overflow: hidden;
  }
  .cover-art { position: absolute; inset: 0; width: 740px; height: 1110px; }
  .tagline-arc {
    font-family: "Montserrat", sans-serif; font-weight: 500;
    font-size: 13px; letter-spacing: 5px; fill: var(--ink);
  }
  .author-arc {
    font-family: "Montserrat", sans-serif; font-weight: 400;
    font-size: 40px; letter-spacing: 22px; fill: var(--ink);
  }
  .title {
    position: absolute; left: 0; right: 0; top: 200px;
    text-align: center; font-family: "Abril Fatface", serif; line-height: .82;
  }
  .title-the { display: block; font-size: 84px; color: var(--ink); margin-left: 90px; }
  .title-main { display: block; font-size: 138px; color: var(--ink); letter-spacing: -2px; }
  .title-accent {
    display: block; font-size: 150px; letter-spacing: -2px;
    background: linear-gradient(90deg, var(--teal) 0%, var(--teal) 55%, var(--teal-deep) 100%);
    -webkit-background-clip: text; background-clip: text; color: transparent;
  }
  .subtitle {
    position: absolute; left: 0; right: 0; top: 585px;
    text-align: center; font-family: "Oswald", sans-serif; font-weight: 600;
    font-size: 25px; line-height: 1.15; color: var(--ink); text-transform: uppercase;
    transform: rotate(-4deg);
  }
</style>
</head>
<body>
  <main class="cover">
    <svg class="cover-art" viewBox="0 0 740 1110" xmlns="http://www.w3.org/2000/svg">
      <defs>
        <path id="tagline-curve" d="M70 300 Q330 150 640 200"/>
        <path id="author-curve" d="M110 1070 Q420 1050 710 975"/>
        <linearGradient id="flow-art-fill" x1="0" y1="0" x2="1" y2="0.4">
          <stop offset="0" stop-color="#e77f95"/>
          <stop offset=".35" stop-color="#8a7fc0"/>
          <stop offset=".65" stop-color="#c7cf3d"/>
          <stop offset="1" stop-color="#38c6c2"/>
        </linearGradient>
      </defs>
      <text class="tagline-arc"><textPath href="#tagline-curve">UNLOCK PERFORMANCE, SPARK ENGAGEMENT:</textPath></text>
      <rect class="flow-art" x="110" y="715" width="520" height="235" rx="30"
            fill="url(#flow-art-fill)" opacity=".75"
            role="img" aria-label="Flow methodology illustration: colour wheels in an infinity loop with a compass and team figures"/>
      <text class="author-arc"><textPath href="#author-curve">JORIN VALKEMA</textPath></text>
    </svg>
    <h1 class="title">
      <span class="title-the">The</span>
      <span class="title-main">Vantor</span>
      <span class="title-accent">Codex</span>
    </h1>
    <p class="subtitle">Master the art of building winning<br>cultures in today's hybrid world</p>
  </main>
</body>
</html>
```